Business Card Design Project

We are not a new company, but renamed to "Vantorin Kitchens" last year. We specialize in modern high-end cabinetry imports. We would like to communicate a sense of quality and cutting edge technology. Ideally the design would incorporate our logo colors, silver, red and preferably a black, matte background. Though we are open to suggestions.
Logo is attached.
Edit: I have attached rough drafts of the previous cards, this way you will have all necessary content that needs to go on the cards.
Updates
Project Deadline Extended
Reason: We have received a lot of great designs, but due to the sheer number we couldn't respond to all. We will extend the deadline for another 7 days to finalize and provide feedback to designers.
Thank you for your hard work!
Industry/Entity Type
Business
Look and feel
Each slider illustrates characteristics of the customer's brand and the style your logo design should communicate.

```html
<!DOCTYPE html>
<html lang="en">
<head>
<meta charset="utf-8">
<title>Vantorin Kitchens – Business Cards</title>
<link href="https://fonts.googleapis.com/css2?family=Arimo:wght@400;700&family=PT+Sans&display=swap" rel="stylesheet">
<style>
  :root {
    --stage: #8a5f3e;
    --card-black: #141516;
    --card-black-top: #1e2022;
    --silver: #c9cbcd;
    --silver-dark: #8f9295;
    --ink-light: #ffffff;
    --label: #1a120c;
    --red: #d6262a;
  }
  * { margin: 0; padding: 0; box-sizing: border-box; }
  html, body { width: 1200px; height: 788px; overflow: hidden; }
  body {
    position: relative;
    background: var(--stage);
    font-family: "Arimo", Arial, sans-serif;
  }
  .side-label {
    position: absolute;
    width: 300px;
    text-align: center;
    font-family: "PT Sans", sans-serif;
    font-size: 21px;
    color: var(--label);
  }
  .card {
    position: absolute;
    width: 525px;
    height: 300px;
    border-radius: 18px;
    overflow: hidden;
    background: linear-gradient(180deg, var(--card-black-top) 0%, var(--card-black) 100%);
    box-shadow: 0 3px 8px rgba(0,0,0,.45);
    color: var(--ink-light);
  }
  .swoosh { position: absolute; inset: 0; }
  .brand {
    position: absolute;
    font-weight: 700;
    font-size: 25px;
    letter-spacing: 1.5px;
    text-transform: uppercase;
    color: var(--silver);
    white-space: nowrap;
  }
  .brand-mark {
    position: absolute;
    width: 46px;
    height: 46px;
    background: var(--silver-dark);
  }
  .contact {
    position: absolute;
    left: 30px;
    top: 132px;
    font-size: 13px;
    line-height: 20.5px;
  }
  .person { font-size: 15px; margin-bottom: 8px; }
  .person .name { font-weight: 700; }
  .person .name.plain { font-weight: 400; }
  .person .role { font-size: 14px; }
  .person .role.small { font-size: 12.5px; }
  .contact dt { display: inline; font-weight: 700; }
  .contact .email { margin-top: 6px; }
  .contact .address { margin-top: 7px; }
  .pattern {
    position: absolute;
    role: img;
  }
  .pattern-top {
    left: 0; top: 0; width: 260px; height: 90px;
    background: radial-gradient(ellipse at 50% 0%, #5a5c5f 0%, #2a2b2d 55%, transparent 100%);
  }
  .pattern-bottom {
    right: 0; bottom: 0; width: 250px; height: 90px;
    background: radial-gradient(ellipse at 55% 100%, #5a5c5f 0%, #2a2b2d 55%, transparent 100%);
  }
  .card-back-alt { background: #0b0b0c; }
</style>
</head>
<body>

<div class="side-label" style="left:157px; top:22px;">front</div>
<div class="side-label" style="left:752px; top:22px;">front-1</div>
<div class="side-label" style="left:164px; top:405px;">back</div>
<div class="side-label" style="left:745px; top:405px;">Back - 1</div>

<!-- front -->
<section class="card" style="left:53px; top:74px;">
  <svg class="swoosh" width="525" height="300" viewBox="0 0 525 300" aria-hidden="true">
    <defs>
      <linearGradient id="silverA" x1="0" y1="0" x2="1" y2="1">
        <stop offset="0" stop-color="#e6e7e8"/><stop offset="1" stop-color="#9a9c9f"/>
      </linearGradient>
    </defs>
    <path d="M362,0 Q478,60 470,200 Q462,70 384,0 Z" fill="url(#silverA)"/>
    <path d="M438,0 Q560,120 440,300 L525,300 L525,0 Z" fill="url(#silverA)"/>
  </svg>
  <span class="brand-mark" style="left:122px; top:22px;"></span>
  <div class="brand" style="left:30px; top:82px;">Vantorin Kitchens</div>
  <div class="contact">
    <p class="person"><span class="name">DORIAN VELL,</span> <span class="role">President</span></p>
    <dl>
      <div><dt>phone</dt> : 555.210.0430</div>
      <div><dt>cell</dt> : 555.318.2276</div>
      <div><dt>fax</dt> : 555.210.0431</div>
    </dl>
    <p class="email">dorian@vantorinkitchens.ca</p>
    <p class="address">1820 - 48 Ave., Northgate, AB T0X 2Q1</p>
  </div>
</section>

<!-- front-1 -->
<section class="card" style="left:620px; top:74px;">
  <svg class="swoosh" width="525" height="300" viewBox="0 0 525 300" aria-hidden="true">
    <defs>
      <linearGradient id="silverB" x1="0" y1="0" x2="1" y2="1">
        <stop offset="0" stop-color="#e6e7e8"/><stop offset="1" stop-color="#9a9c9f"/>
      </linearGradient>
    </defs>
    <path d="M362,0 Q478,60 470,200 Q462,70 384,0 Z" fill="url(#silverB)"/>
    <path d="M438,0 Q560,120 440,300 L525,300 L525,0 Z" fill="url(#silverB)"/>
  </svg>
  <span class="brand-mark" style="left:130px; top:22px;"></span>
  <div class="brand" style="left:37px; top:82px;">Vantorin Kitchens</div>
  <div class="contact" style="left:37px;">
    <p class="person"><span class="name plain">MAREK VELL,</span> <span class="role small">Director</span></p>
    <dl>
      <div><dt>phone</dt> : 555.210.0430</div>
      <div><dt>cell</dt> : 555.318.4092</div>
      <div><dt>fax</dt> : 555.210.0431</div>
    </dl>
    <p class="email">marek@vantorinkitchens.ca</p>
    <p class="address">1820 - 48 Ave., Northgate, AB T0X 2Q1</p>
  </div>
</section>

<!-- back -->
<section class="card" style="left:56px; top:447px;">
  <span class="brand-mark" style="left:205px; top:92px;"></span>
  <div class="brand" style="left:90px; top:158px; font-size:26px;">Vantorin Kitchens</div>
</section>

<!-- back-1 -->
<section class="card card-back-alt" style="left:624px; top:446px;">
  <div class="pattern pattern-top" role="img" aria-label="Perforated metal dot texture fading in from the top left"></div>
  <div class="pattern pattern-bottom" role="img" aria-label="Perforated metal dot texture fading in from the bottom right"></div>
  <span class="brand-mark" style="left:200px; top:94px;"></span>
  <div class="brand" style="left:74px; top:170px; font-size:27px;">Vantorin Kitchens</div>
</section>

</body>
</html>
```